Casino with the 'highest winning percentage' needs a stationery design

This is for a casino in Colombo, Sri Lanka and we need a stationery design for business card, letter head and envelope.

Should be very professional, simple and elegant without fancy fonts

Reason: Not fully satisfied with the designs. Need more designs.

Business

• 1. card deck symbol 'CLUBS' in red, or black

2. name in BLOCK CAPITAL LETTERS

3. Preferred font colours are black, white or red

4. Prefer 'professional /elegant' fonts
• SHOULD NOT HAVE ANY OTHER SYMBOL EXCEPT 'CLUBS'

DO NOT PREFER ITALIC FONTS

```html
<!DOCTYPE html>
<html lang="en">
<head>
<meta charset="utf-8">
<title>Corvane Entertainment – Stationery</title>
<link href="https://fonts.googleapis.com/css2?family=Noto+Serif:wght@700&family=Open+Sans:wght@400;600&family=Jost:wght@400&display=swap" rel="stylesheet">
<style>
  :root {
    --stage: #b97a45;
    --paper: #ffffff;
    --paper-shade: #eeeeee;
    --ink: #1a1a1a;
    --muted: #555555;
    --brand-red: #d0202e;
    --faint-red: #f4e6e7;
    --rule: #444444;
    --label: #ffffff;
    --flap-dark: #0c0c0c;
  }
  * { box-sizing: border-box; margin: 0; padding: 0; }
  html, body { width: 1200px; height: 386px; overflow: hidden; }
  body {
    position: relative;
    background: var(--stage);
    font-family: "Open Sans", Arial, sans-serif;
    color: var(--ink);
  }
  .sheet, .envelope, .card {
    position: absolute;
    background: linear-gradient(160deg, var(--paper) 60%, var(--paper-shade));
    overflow: hidden;
  }
  .sheet { top: 18px; width: 263px; height: 340px; }
  .sheet--one { left: 3px; }
  .sheet--two { left: 282px; }
  .sheet--fax { left: 557px; }

  .brand { position: absolute; display: flex; align-items: center; gap: 6px; }
  .brand__dot { width: 14px; height: 14px; border-radius: 50%; background: var(--brand-red); flex: none; }
  .brand__name {
    font-family: "Noto Serif", Georgia, serif;
    font-weight: 700;
    font-size: 9px;
    line-height: 1.25;
    color: var(--ink);
    letter-spacing: 0.2px;
  }
  .sheet .brand { top: 12px; left: 78px; }
  .sheet--two .brand, .sheet--fax .brand { left: 10px; }

  .faint-mark { position: absolute; border-radius: 50%; background: var(--faint-red); }
  .sheet--one .faint-mark { left: 60px; top: 150px; width: 110px; height: 110px; }
  .sheet--two .faint-mark { right: 6px; bottom: 10px; width: 48px; height: 48px; }

  .corner-info { position: absolute; top: 15px; right: 14px; font-size: 4.5px; line-height: 1.45; color: var(--ink); }
  .corner-info .org { color: var(--brand-red); font-weight: 600; }
  .corner-info .lead { color: var(--brand-red); font-weight: 600; }
  .corner-info .web { color: var(--brand-red); }

  .footer { position: absolute; left: 0; right: 0; text-align: center; font-size: 4.6px; color: var(--ink); line-height: 1.6; }
  .footer .org, .footer .lead, .footer .web { color: var(--brand-red); }
  .sheet--one .footer { bottom: 6px; }
  .sheet--two .footer, .sheet--fax .footer { bottom: 8px; }

  .fax__title { position: absolute; top: 80px; left: 10px; font-family: "Jost", Arial, sans-serif; font-size: 19px; letter-spacing: 0.5px; }
  .fax__fields { position: absolute; top: 109px; left: 10px; right: 30px; display: grid; grid-template-columns: 132px 92px; column-gap: 12px; row-gap: 5px; }
  .fax__field { font-size: 4.8px; border-bottom: 0.6px solid var(--rule); height: 10px; line-height: 10px; }
  .fax__checks { position: absolute; top: 187px; left: 10px; right: 30px; display: flex; justify-content: space-between; font-size: 4.8px; }
  .fax__check { display: flex; align-items: center; gap: 3px; }
  .fax__check::before { content: ""; width: 6px; height: 6px; border: 0.6px solid var(--rule); }

  .envelope--back { left: 902px; top: 4px; width: 264px; height: 132px; }
  .envelope--open { left: 838px; top: 62px; width: 270px; height: 130px; background: var(--paper); }
  .envelope--front { left: 870px; top: 120px; width: 294px; height: 131px; box-shadow: 0 1px 3px rgba(0,0,0,0.25); }
  .envelope__flap { position: absolute; inset: 0; width: 100%; height: 100%; }
  .envelope__seal { position: absolute; width: 16px; height: 16px; border-radius: 50%; background: var(--brand-red); }
  .envelope--back .envelope__seal { left: 124px; top: 14px; }
  .envelope--open .envelope__seal { left: 136px; top: 14px; }
  .envelope--front .brand { top: 10px; left: 10px; }
  .envelope--front .brand__dot { width: 20px; height: 20px; }
  .envelope--front .brand__name { font-size: 10px; }
  .envelope__address { position: absolute; top: 36px; left: 42px; font-size: 5px; line-height: 1.5; color: var(--ink); }
  .envelope--front .faint-mark { right: 16px; top: 50px; width: 72px; height: 72px; }
  .envelope__web { position: absolute; left: 42px; bottom: 6px; font-size: 5px; letter-spacing: 1.2px; color: var(--muted); }
  .envelope__web span { color: var(--brand-red); }

  .card { top: 269px; width: 160px; height: 89px; box-shadow: 0 1px 2px rgba(0,0,0,0.25); }
  .card--contact { left: 862px; }
  .card--tagline { left: 1035px; }
  .card--contact .brand { top: 7px; left: 12px; }
  .card__details { position: absolute; top: 37px; left: 12px; font-size: 4.2px; line-height: 1.55; }
  .card__details .org, .card__details .lead, .card__details .web { color: var(--brand-red); font-weight: 600; }
  .card--contact .faint-mark { right: 14px; top: 40px; width: 46px; height: 46px; }
  .card--tagline .brand { top: 27px; left: 20px; }
  .card--tagline .brand__dot { width: 22px; height: 22px; }
  .card--tagline .brand__name { font-size: 10px; }
  .card__tagline { position: absolute; left: 0; right: 0; top: 63px; text-align: center; font-family: "Noto Serif", Georgia, serif; font-weight: 700; font-size: 5px; letter-spacing: 0.4px; color: var(--brand-red); }

  .option-label { position: absolute; top: 361px; font-size: 18px; color: var(--label); font-family: "Open Sans", Arial, sans-serif; }
  .option-label--one { left: 90px; }
  .option-label--two { left: 367px; }
  .option-label--three { left: 642px; }
</style>
</head>
<body>

  <section class="sheet sheet--one" aria-label="Letterhead option one">
    <div class="brand"><span class="brand__dot"></span><span class="brand__name">CORVANE<br>ENTERTAINMENT</span></div>
    <div class="faint-mark" role="img" aria-label="Faint brand mark decoration"></div>
    <div class="footer">
      <div><span class="org">CORVANE LIMITED</span> 52, Harbour View Road, Colombo 01000, Sri Lanka</div>
      <div><span class="lead">P</span> + 94 11 2450780 &nbsp;<span class="lead">F</span> + 94 11 2450781 &nbsp;<span class="lead">E</span> info@corvanecolombo.com &nbsp;www.corvanecolombo.com</div>
    </div>
  </section>

  <section class="sheet sheet--two" aria-label="Letterhead option two">
    <div class="brand"><span class="brand__dot"></span><span class="brand__name">CORVANE<br>ENTERTAINMENT</span></div>
    <div class="corner-info">
      <div class="org">CORVANE LIMITED</div>
      <div>52, Harbour View Road</div>
      <div>Colombo 01000, Sri Lanka</div>
    </div>
    <div class="faint-mark" role="img" aria-label="Faint brand mark decoration"></div>
    <div class="footer"><span class="lead">P :</span> + 94 11 2450780 &nbsp;<span class="lead">F :</span> + 94 11 2450781 &nbsp;<span class="lead">E :</span> info@corvanecolombo.com &nbsp;<span class="web">www.corvanecolombo.com</span></div>
  </section>

  <section class="sheet sheet--fax" aria-label="Fax sheet">
    <div class="brand"><span class="brand__dot"></span><span class="brand__name">CORVANE<br>ENTERTAINMENT</span></div>
    <div class="corner-info">
      <div><span class="lead">P :</span> + 94 11 2450780</div>
      <div><span class="lead">F :</span> + 94 11 2450781</div>
      <div><span class="lead">E :</span> info@corvanecolombo.com</div>
      <div class="web">www.corvanecolombo.com</div>
    </div>
    <h1 class="fax__title">FAX</h1>
    <div class="fax__fields">
      <div class="fax__field">To :</div><div class="fax__field">From :</div>
      <div class="fax__field">Fax :</div><div class="fax__field">Pages :</div>
      <div class="fax__field">Phone :</div><div class="fax__field">Date :</div>
      <div class="fax__field">Re :</div><div class="fax__field">CC :</div>
    </div>
    <div class="fax__checks">
      <span class="fax__check">Urgent</span>
      <span class="fax__check">For Review</span>
      <span class="fax__check">Please Comment</span>
      <span class="fax__check">Please Reply</span>
      <span class="fax__check">Please Recycle</span>
    </div>
    <div class="footer"><span class="org">CORVANE LIMITED</span> 52, Harbour View Road, Colombo 01000, Sri Lanka</div>
  </section>

  <section class="envelope envelope--back" aria-label="Envelope back">
    <svg class="envelope__flap" viewBox="0 0 264 132" preserveAspectRatio="none" aria-hidden="true">
      <polygon points="0,0 264,0 264,20 132,62 0,20" fill="var(--flap-dark)"/>
    </svg>
    <span class="envelope__seal"></span>
  </section>

  <section class="envelope envelope--open" aria-label="Envelope with open flap">
    <svg class="envelope__flap" viewBox="0 0 270 130" preserveAspectRatio="none" aria-hidden="true">
      <polygon points="1,1 269,1 269,22 140,60 1,22" fill="none" stroke="#555" stroke-width="0.8"/>
    </svg>
    <span class="envelope__seal"></span>
  </section>

  <section class="envelope envelope--front" aria-label="Envelope front">
    <div class="brand"><span class="brand__dot"></span><span class="brand__name">CORVANE<br>ENTERTAINMENT</span></div>
    <div class="envelope__address">52, Harbour View Road<br>Colombo 01000, Sri Lanka</div>
    <div class="faint-mark" role="img" aria-label="Faint brand mark decoration"></div>
    <div class="envelope__web">www.<span>corvanecolombo</span>.com</div>
  </section>

  <section class="card card--contact" aria-label="Business card front">
    <div class="brand"><span class="brand__dot"></span><span class="brand__name">CORVANE<br>ENTERTAINMENT</span></div>
    <div class="card__details">
      <div class="org">CORVANE LIMITED</div>
      <div>52, Harbour View Road</div>
      <div>Colombo 01000, Sri Lanka</div>
      <div style="margin-top:2px"><span class="lead">P :</span> + 94 11 2450780</div>
      <div><span class="lead">C :</span> + 94 77 3158420</div>
      <div><span class="lead">F :</span> + 94 11 2450781</div>
      <div><span class="lead">E :</span> info@corvanecolombo.com</div>
      <div class="web">www.corvanecolombo.com</div>
    </div>
    <div class="faint-mark" role="img" aria-label="Faint brand mark decoration"></div>
  </section>

  <section class="card card--tagline" aria-label="Business card back">
    <div class="brand"><span class="brand__dot"></span><span class="brand__name">CORVANE<br>ENTERTAINMENT</span></div>
    <p class="card__tagline">HIGHEST WINNING PERCENTAGE IN THE WORLD</p>
  </section>

  <span class="option-label option-label--one">Option-1</span>
  <span class="option-label option-label--two">Option-2</span>
  <span class="option-label option-label--three">Option-3</span>

</body>
</html>
```